Packaging label for spirit line

We currently have a various line of spirits and are looking to rebrand the label. The bottle would stay the same since there is a lot of stock. An example of the current situation has been attached. The entire collection is to be found on our website: www.quillhouse.brindlework.be/spirits

These spirits are a product created by our cocktail bar "Velvet Parlour". The name however, would likely change to "Nightwagger" or plural "Nightwaggers" since we'd like to split those 2 businesses. The series "bartender series" would remain the same as it is a complete series mainly invented for mixology.

The current label is fine, but needs that extra spark that makes it stand out on a shelve compared to other spirit bottles. We envision a more funky yet sophisticated branding with perhaps goldtrims for that "exclusive, luxurious" feel and very much like a vintage animal humification vibe (for example: the peculiar or quince's). Preferably a french bulldog as this has been our mascotte since the very beginning of starting this business.

Last but not least, the measurements: max. 90 mm height and max. 260 mm length. The current label is 90x180mm. 260mm means the label goes fully around the bottle.

Industry/Entity Type

Alcoholic Beverages

Font styles to use
Serif
Sans Serif

Requirements
Must have
• The label must have the standard information such as the product name, the alcohol %, the volume ml and room for ean code. The bottle needs to be sealed for shipment, so a little seal to cover the lid is required.
Nice to have
• It would be nice to maintain consistency with for example the same animal but change of background / colors / outfit / etc to clarify the different flavors. A cutout/contour is also preferable for added interest, so that the label is not square.
Should not have
• The label should definitely not be childish or too much. The overal look and feel needs to be professional yet not too serious.

```html
<!DOCTYPE html>
<html lang="en">
<head>
<meta charset="utf-8">
<title>Nightwagger London Dry Gin – Herbwise label</title>
<link href="https://fonts.googleapis.com/css2?family=Anton&family=Cinzel:wght@500&family=Libre+Caslon+Text:wght@400;700&family=Yellowtail&family=Oswald:wght@500;600&display=swap" rel="stylesheet">
<style>
  :root{
    --backdrop:#eeede6;
    --paper:#e4e5d8;
    --paper-line:#d9dacb;
    --gold:#c9a24a;
    --brown-ink:#6b5a47;
    --green-ink:#4f8a3c;
    --green-band:#5c9347;
    --green-dark:#477f35;
    --sand-band:#a38e70;
    --earth-band:#7c6a55;
    --white:#ffffff;
    --illus-light:#d8cbb4;
    --illus-dark:#8d7d69;
  }
  *{margin:0;padding:0;box-sizing:border-box}
  html,body{width:1200px;height:1056px;overflow:hidden;background:var(--backdrop)}
  .canvas{position:relative;width:1200px;height:1056px}

  /* neck seal strip */
  .neck-seal{
    position:absolute;left:80px;top:260px;width:80px;height:460px;
    background:var(--paper);border:1px solid var(--paper-line);
    display:flex;flex-direction:column;align-items:center;justify-content:flex-end;padding-bottom:20px;
  }
  .neck-seal__name{
    font-family:'Anton',sans-serif;font-size:40px;color:var(--brown-ink);
    writing-mode:vertical-rl;transform:rotate(180deg);letter-spacing:1px;margin-bottom:16px;
  }
  .neck-seal__sub{
    font-family:'Libre Caslon Text',serif;font-size:11px;color:var(--green-ink);text-align:center;line-height:1.25;
  }

  /* main label */
  .label{
    position:absolute;left:240px;top:108px;width:900px;height:840px;overflow:hidden;
    background:repeating-linear-gradient(90deg,var(--paper) 0 3px,var(--paper-line) 3px 4px);
  }
  .label__trim{position:absolute;left:0;right:0;height:2px;background:var(--gold)}
  .label__trim--a{top:10px}
  .label__trim--b{top:28px;height:1.5px}

  .label__mascot{
    position:absolute;left:0;top:44px;width:330px;height:756px;z-index:3;
    background:linear-gradient(180deg,var(--illus-light) 0%,var(--illus-dark) 60%,var(--illus-light) 100%);
    border-radius:0 120px 30px 0;
  }

  .label__text{position:absolute;left:350px;width:530px;text-align:center}
  .label__club{top:48px;font-family:'Yellowtail',cursive;font-size:40px;line-height:1.2;color:var(--green-ink)}
  .label__brand{
    top:116px;font-family:'Anton',sans-serif;font-size:84px;line-height:1;color:var(--brown-ink);
    transform:scaleY(1.5);transform-origin:top center;
  }
  .label__category{top:290px;font-family:'Cinzel',serif;font-weight:500;font-size:44px;line-height:1.2;color:var(--green-ink)}
  .label__story{top:372px;font-family:'Libre Caslon Text',serif;font-size:24px;line-height:1.45;color:var(--brown-ink)}

  .flavor-band{
    position:absolute;left:200px;right:0;top:520px;height:150px;background:var(--green-band);display:flex;
  }
  .flavor-band__number{
    width:130px;margin-left:140px;background:var(--green-dark);color:var(--white);
    font-family:'Libre Caslon Text',serif;font-size:46px;line-height:1.05;
    display:flex;flex-direction:column;align-items:center;justify-content:center;
  }
  .flavor-band__name{flex:1;display:flex;flex-direction:column;justify-content:center;padding-left:40px}
  .flavor-band__title{
    font-family:'Libre Caslon Text',serif;font-weight:700;font-size:46px;color:var(--white);letter-spacing:1px;line-height:1.1;
    padding-bottom:10px;border-bottom:2px dashed rgba(255,255,255,.6);width:330px;
  }
  .flavor-band__type{font-family:'Libre Caslon Text',serif;font-size:26px;color:var(--white);letter-spacing:3px;margin-top:10px}

  .series-band{
    position:absolute;left:0;right:0;top:670px;height:140px;background:var(--sand-band);
    color:var(--white);text-align:center;padding-left:340px;
  }
  .series-band__line{font-family:'Oswald',sans-serif;font-weight:600;font-size:21px;letter-spacing:1.5px;margin-top:40px}
  .series-band__spec{font-family:'Oswald',sans-serif;font-weight:500;font-size:21px;margin-top:6px}
  .base-band{position:absolute;left:0;right:0;top:810px;height:30px;background:var(--earth-band)}
</style>
</head>
<body>
<div class="canvas">

  <div class="neck-seal">
    <span class="neck-seal__name">NIGHTWAGGER</span>
    <span class="neck-seal__sub">LONDON<br>DRY GIN</span>
  </div>

  <div class="label">
    <div class="label__trim label__trim--a"></div>
    <div class="label__trim label__trim--b"></div>

    <div class="label__text label__club">Velvet Parlour</div>
    <div class="label__text label__brand">NIGHTWAGGER</div>
    <div class="label__text label__category">LONDON DRY GIN</div>
    <p class="label__text label__story">Finely distilled herbal gin<br>balanced mix of botanicals<br>with thyme as ruler.</p>

    <div class="flavor-band">
      <div class="flavor-band__number"><span>NO</span><span>01</span></div>
      <div class="flavor-band__name">
        <div class="flavor-band__title">HERBWISE</div>
        <div class="flavor-band__type">DISTILLED SPIRIT</div>
      </div>
    </div>

    <div class="series-band">
      <div class="series-band__line">BARTENDER&nbsp; SERIES BY VELVET PARLOUR</div>
      <div class="series-band__spec">500ML | 38.0% VOL. ALC.</div>
    </div>
    <div class="base-band"></div>

    <div class="label__mascot" role="img" aria-label="Illustration of a French bulldog mascot in round sunglasses, white shirt and brown overalls, leaning on a bar"></div>
  </div>

</div>
</body>
</html>
```